Bramwell IT Services Business Card

Bramwell IT Services are a Perth based IT Services company. We would like to incorporate our company logo (attached) and stick with the blue that is in that design. I would like a clean look design that isn't too busy, yet creates a lasting image that is instantly recognisable in the recipients mind.

Target Market(s)

The target audience is small/medium business owners.

Industry/Entity Type

Business

Font styles to use
Serif
Sans Serif

Colors

Designer to choose colors to be used in the design.

Requirements
Must have
• The design should include:
Business name: Bramwell IT Services
Directors Name: Marcus Tenley
Phone Number: 0483 562 904
Email: support@bramwellit.com.au
Website: www.bramwellit.com.au

```html
<!DOCTYPE html>
<html lang="en">
<head>
<meta charset="utf-8">
<title>Bramwell IT Services – Business Card</title>
<link rel="stylesheet" href="https://fonts.googleapis.com/css2?family=Arimo:wght@400;700&display=swap">
<style>
  :root {
    --stage: #d6d6d6;
    --blue-deep: #0a3a86;
    --blue-mid: #1553a6;
    --blue-light: #2a6fc4;
    --navy: #1c3565;
    --band-dark: #3c3d42;
    --swoosh-grey: #a9abb0;
    --ink: #222222;
    --white: #ffffff;
  }
  * { margin: 0; padding: 0; box-sizing: border-box; }
  html, body { width: 1200px; height: 900px; overflow: hidden; }
  body {
    background: var(--stage);
    font-family: "Arimo", Arial, sans-serif;
    position: relative;
  }
  .card {
    position: absolute;
    left: 250px;
    width: 700px;
    height: 400px;
    overflow: hidden;
    box-shadow: 0 6px 18px rgba(0,0,0,0.25);
  }
  .card-back {
    top: 40px;
    background: radial-gradient(ellipse at 48% 42%, var(--blue-light) 0%, var(--blue-mid) 40%, var(--blue-deep) 100%);
    display: flex;
    flex-direction: column;
    align-items: center;
    justify-content: center;
    gap: 10px;
  }
  .card-front {
    top: 460px;
    background: var(--white);
  }
  .card-front .waves { position: absolute; inset: 0; width: 700px; height: 400px; }

  .brand {
    display: flex;
    align-items: center;
    gap: 12px;
    font-weight: 700;
    font-size: 30px;
    letter-spacing: 0.5px;
    text-transform: uppercase;
  }
  .brand-mark { width: 22px; height: 22px; }
  .card-back .brand { color: var(--white); }
  .card-back .brand-mark { background: var(--white); }
  .card-back .web { color: var(--white); font-size: 17px; }

  .card-front .brand {
    position: absolute;
    left: 40px;
    top: 160px;
    color: var(--blue-mid);
    font-size: 28px;
  }
  .card-front .brand-mark { background: var(--blue-mid); }

  .person {
    position: absolute;
    right: 110px;
    top: 42px;
    text-align: right;
  }
  .person .name { color: var(--blue-mid); font-size: 21px; }
  .person .role { color: var(--ink); font-size: 14px; margin-top: 2px; }

  .contacts {
    position: absolute;
    left: 40px;
    bottom: 28px;
    list-style: none;
    color: var(--white);
    font-size: 16px;
  }
  .contacts li { display: flex; align-items: center; gap: 10px; height: 24px; }
  .contacts svg { width: 15px; height: 15px; fill: none; stroke: var(--white); stroke-width: 1.6; }
</style>
</head>
<body>

<section class="card card-back" aria-label="Card back">
  <div class="brand"><span class="brand-mark"></span>Bramwell IT Services</div>
  <p class="web">www.bramwellit.com.au</p>
</section>

<section class="card card-front" aria-label="Card front">
  <svg class="waves" viewBox="0 0 700 400" aria-hidden="true">
    <defs>
      <linearGradient id="blueBand" x1="0" y1="1" x2="1" y2="0">
        <stop offset="0" stop-color="#1f62b8"/>
        <stop offset="0.6" stop-color="#1a4a95"/>
        <stop offset="1" stop-color="#1c3565"/>
      </linearGradient>
    </defs>
    <path fill="var(--swoosh-grey)" d="M330,250 C450,210 540,150 600,110 C630,92 665,88 700,88 L700,112 C650,112 610,130 560,165 C480,220 410,245 330,260 Z"/>
    <path fill="var(--band-dark)" d="M0,268 C180,262 330,230 450,185 L455,200 C330,252 180,282 0,290 Z"/>
    <path fill="url(#blueBand)" d="M0,296 C200,288 380,240 520,170 C590,135 640,118 700,116 L700,400 L0,400 Z"/>
  </svg>

  <div class="person">
    <p class="name">Marcus Tenley</p>
    <p class="role">Director</p>
  </div>

  <div class="brand"><span class="brand-mark"></span>Bramwell IT Services</div>

  <ul class="contacts">
    <li>
      <svg viewBox="0 0 16 16" aria-hidden="true"><path d="M3 2h3l1 3-2 1a8 8 0 0 0 5 5l1-2 3 1v3c-6 1-12-5-11-11z"/></svg>
      0483 562 904
    </li>
    <li>
      <svg viewBox="0 0 16 16" aria-hidden="true"><rect x="1.5" y="3.5" width="13" height="9"/><path d="M1.5 3.5l6.5 5 6.5-5"/></svg>
      support@bramwellit.com.au
    </li>
    <li>
      <svg viewBox="0 0 16 16" aria-hidden="true"><circle cx="8" cy="8" r="6.5"/><ellipse cx="8" cy="8" rx="3" ry="6.5"/><path d="M1.5 8h13"/></svg>
      www.bramwellit.com.au
    </li>
  </ul>
</section>

</body>
</html>
```